AMAZING WEBSITE DESIGN NEEDED FOR MAID / CLEANING SERVICE

NOTE: This is Website Design Only - No coding required

Please submit your designs ASAP as we want to pick a winner and get started!

Hey,

We are looking for a new amazing website design for a maid or cleaning service.

They have a horrible website that we want turned into a masterpiece.

As you will see on their current site:

http://brightnookservices.example-host.net/

They have a lot of stuff, very disorganized, and need help.

Here is what we need:

Colors: Same as current site, Orange, Gray, Black

Menu: Horizontal with same Menu items

Need a spot for a video on the homepage

Want content to be structured in a great format that is easy to read.

Want to highlight commercial and residential on the website homepage.

Also want a spot for customer testimonials

We want the site clean, professional, fresh and modern.

Please help by matching the logo design.

I look forward to your designs!
Updates

Hi All! Really appreciate your efforts and designs. I will be meeting with our client on Monday and will then be able to provide feedback after our meeting. If you have other ideas, please submit them. The more I can show him the better! Thanks!

Target Market(s)

The target market is residential home owners as well as commercial businesses who need cleaning on a regular basis.

This company cleans homes and offices for individuals.

Industry/Entity Type

Residential

Font styles to use
Sans Serif

Requirements
Must have
• Must match logo colors
Must have spot for video
Must have a clean look
Must have a bold look
Nice to have
• Highly visual
Should not have
• clutter
messy design
hard to read

```html
<!DOCTYPE html>
<html lang="en">
<head>
<meta charset="utf-8">
<title>Bright Nook – Quality Commercial &amp; Residential Cleaning</title>
<link href="https://fonts.googleapis.com/css2?family=Open+Sans:wght@300;400;600;700&display=swap" rel="stylesheet">
<style>
:root{
  --orange:#f07f1e;
  --orange-dark:#e0701a;
  --ink:#3d3d3d;
  --text:#5a5a5a;
  --muted:#8a8a8a;
  --light:#f2f2f2;
  --footer:#565656;
  --white:#ffffff;
}
*{margin:0;padding:0;box-sizing:border-box}
html,body{width:845px;height:1200px;overflow:hidden}
body{font-family:"Open Sans",Arial,sans-serif;background:var(--white);color:var(--text);position:relative}
.abs{position:absolute}

.main-nav{left:0;top:0;width:845px;height:42px;background:var(--orange)}
.main-nav ul{list-style:none;display:flex;position:absolute;left:91px;top:0;height:42px;align-items:center}
.main-nav li{font-size:10px;color:var(--white);margin-right:16.5px;position:relative;height:42px;line-height:46px}
.main-nav li.active::after{content:"";position:absolute;left:-5px;right:-5px;bottom:0;height:2px;background:var(--white)}

.call-us{left:77px;top:97px;display:flex;align-items:center;font-size:12px;color:var(--orange)}
.call-us .phone-icon{width:19px;height:18px;background:var(--orange);border-radius:2px;margin-right:7px;display:flex;align-items:center;justify-content:center}
.call-us strong{color:var(--ink);font-weight:600;margin-left:6px}

.brand{left:340px;top:86px;width:200px;text-align:center}
.brand .name{font-size:25px;font-weight:700;color:var(--orange);letter-spacing:-.5px;display:flex;align-items:center;justify-content:center;gap:7px}
.brand .name .mark{width:12px;height:12px;background:var(--ink)}
.brand .tagline{font-size:8px;color:var(--muted);margin-top:2px}

.follow{left:611px;top:98px;display:flex;align-items:center;font-size:12px;color:var(--orange)}
.follow .dot{width:17px;height:17px;border-radius:50%;margin-left:7px}
.follow span{margin-right:7px}

.hero{left:0;top:146px;width:845px;height:344px;background:linear-gradient(90deg,#8a6a4a 0%,#d9cbb8 30%,#f1ece6 55%,#e4e0dc 80%,#bfa98c 100%)}
.hero-title{left:67px;top:260px;width:287px;height:70px;background:rgba(255,255,255,.72);padding:7px 0 0 12px;font-size:23px;font-weight:300;line-height:30px;color:var(--ink)}
.hero-title b{font-weight:700}

.service-card{top:515px;width:330px;height:125px}
.service-card.residential{left:78px;background:linear-gradient(90deg,#d9a26c 0%,#e6b98a 45%,#eedc5a 70%,#d8b27e 100%)}
.service-card.commercial{left:438px;background:linear-gradient(90deg,#3a4257 0%,#8d93a3 45%,#c6c7cc 100%)}
.service-card h2{position:absolute;font-weight:400;font-size:20px;line-height:25px;color:var(--ink)}
.residential h2{left:5px;top:21px}
.commercial h2{right:9px;top:22px;text-align:right}
.btn{position:absolute;top:88px;width:97px;height:25px;background:var(--orange);color:var(--white);font-size:12px;text-align:center;line-height:25px;border-radius:2px}
.residential .btn{left:6px}
.commercial .btn{right:9px}

.why-band{left:0;top:664px;width:845px;height:253px;background:var(--light)}
.section-title{font-size:20px;font-weight:400;color:var(--ink)}
.why-title{left:77px;top:684px}
.video-title{left:434px;top:684px}
.why-list{left:77px;top:732px;list-style:none}
.why-list li{display:flex;align-items:center;height:23.2px;font-size:9.6px;color:var(--text)}
.why-list svg{margin-right:12px}

.video{left:436px;top:732px;width:331px;height:162px;background:linear-gradient(135deg,#cfc8c0 0%,#ece8e3 45%,#d4cdc4 100%)}
.video .play{position:absolute;left:135px;top:59px;width:66px;height:40px;background:rgba(30,30,30,.85);border-radius:4px;display:flex;align-items:center;justify-content:center}
.video .controls{position:absolute;left:5px;right:7px;bottom:4px;height:20px;background:rgba(20,20,20,.85);border-radius:2px}
.video .bar{position:absolute;left:45px;right:65px;top:8px;height:4px;background:#555}
.video .bar i{display:block;width:26%;height:100%;background:#1fa9e1}

.testimonials-title{left:0;top:935px;width:845px;text-align:center}
.testimonial{top:990px;width:332px;height:80px}
.testimonial.first{left:78px}
.testimonial.second{left:435px}
.testimonial .avatar{position:absolute;left:0;top:0;width:68px;height:68px;border-radius:50%;background:linear-gradient(160deg,#f0e3c6,#3c3a40);border:2px solid var(--white);box-shadow:0 0 0 1px #e2e2e2}
.testimonial p{position:absolute;left:81px;top:7px;width:256px;font-size:9.8px;line-height:13.6px;color:var(--muted)}
.testimonial .author{position:absolute;right:0;top:69px;font-size:10px;color:var(--orange)}

.site-footer{left:0;top:1097px;width:845px;height:103px;background:var(--footer)}
.footer-brand{left:78px;top:1130px;color:var(--white)}
.footer-brand .name{font-size:25px;font-weight:700;display:flex;align-items:center;gap:7px}
.footer-brand .name .mark{width:12px;height:12px;background:var(--white)}
.footer-brand .tagline{font-size:8px;margin-top:2px;padding-left:19px}
.footer-info{right:77px;top:1132px;text-align:right;color:var(--white);font-size:10.4px;line-height:20.5px}
</style>
</head>
<body>

<nav class="main-nav abs">
  <ul>
    <li class="active">Home</li><li>Our Services</li><li>Our Employees</li><li>Why Us</li><li>Testimonials</li><li>Special Offers</li><li>About Us</li><li>Contact Us</li><li>Request a Bid</li><li>Meet the President</li>
  </ul>
</nav>

<div class="call-us abs">
  <div class="phone-icon">
    <svg width="11" height="11" viewBox="0 0 24 24"><path fill="#fff" d="M6.6 10.8a15 15 0 0 0 6.6 6.6l2.2-2.2a1 1 0 0 1 1-.25 11.4 11.4 0 0 0 3.6.57 1 1 0 0 1 1 1V20a1 1 0 0 1-1 1A17 17 0 0 1 3 4a1 1 0 0 1 1-1h3.5a1 1 0 0 1 1 1c0 1.25.2 2.45.57 3.57a1 1 0 0 1-.25 1z"/></svg>
  </div>
  Call Us Now: <strong>(505) 555-0172</strong>
</div>

<div class="brand abs">
  <div class="name"><span class="mark"></span>Bright Nook</div>
  <div class="tagline">Quality Commercial &amp; Residential Cleaning</div>
</div>

<div class="follow abs">
  <span>Follow Us:</span>
  <i class="dot" style="background:#1f5f99"></i>
  <i class="dot" style="background:#d93b2b"></i>
  <i class="dot" style="background:#3b5b98"></i>
  <i class="dot" style="background:#2fa6e0"></i>
</div>

<div class="hero abs" role="img" aria-label="Housekeeper arranging pillows on a white sofa in a bright living room"></div>
<h1 class="hero-title abs" style="font-weight:300">Let Us Do The <b>Cleaning</b><br>You Do The <b>Relaxing</b></h1>

<section class="service-card residential abs" role="img" aria-label="Yellow gloved hand wiping a wooden surface with a blue cloth">
  <h2>Residential<br>Cleaning</h2>
  <span class="btn">View More</span>
</section>
<section class="service-card commercial abs" role="img" aria-label="Worker polishing a tiled floor with a yellow machine">
  <h2>Commercial<br>Cleaning</h2>
  <span class="btn">View More</span>
</section>

<div class="why-band abs"></div>
<h2 class="section-title why-title abs">Why Choose Us?</h2>
<h2 class="section-title video-title abs">Featured Video</h2>

<ul class="why-list abs">
  <li><svg width="11" height="9" viewBox="0 0 11 9"><path d="M1 4.5l3 3L10 1" stroke="#f07f1e" stroke-width="2" fill="none"/></svg>We clean and scrub ovens until they shine with perfection!</li>
  <li><svg width="11" height="9" viewBox="0 0 11 9"><path d="M1 4.5l3 3L10 1" stroke="#f07f1e" stroke-width="2" fill="none"/></svg>We wash, dry, iron, and hang/fold all of your laundry!</li>
  <li><svg width="11" height="9" viewBox="0 0 11 9"><path d="M1 4.5l3 3L10 1" stroke="#f07f1e" stroke-width="2" fill="none"/></svg>we will also wash and make your car sparkle!!</li>
  <li><svg width="11" height="9" viewBox="0 0 11 9"><path d="M1 4.5l3 3L10 1" stroke="#f07f1e" stroke-width="2" fill="none"/></svg>we can, and are able, to provide minor carpet cleaning services!</li>
  <li><svg width="11" height="9" viewBox="0 0 11 9"><path d="M1 4.5l3 3L10 1" stroke="#f07f1e" stroke-width="2" fill="none"/></svg>Bright Nook offers their customers choices</li>
  <li><svg width="11" height="9" viewBox="0 0 11 9"><path d="M1 4.5l3 3L10 1" stroke="#f07f1e" stroke-width="2" fill="none"/></svg>We are available 24 hours a day 7 days a week ready to work!</li>
  <li><svg width="11" height="9" viewBox="0 0 11 9"><path d="M1 4.5l3 3L10 1" stroke="#f07f1e" stroke-width="2" fill="none"/></svg>We can supply all cleaning supplies and janitorial supplies!</li>
</ul>

<div class="video abs" role="img" aria-label="Video still of a woman mopping a bright living room floor">
  <div class="play"><svg width="18" height="20" viewBox="0 0 18 20"><path d="M0 0l18 10L0 20z" fill="#fff"/></svg></div>
  <div class="controls">
    <svg style="position:absolute;left:14px;top:5px" width="9" height="10" viewBox="0 0 9 10"><path d="M0 0l9 5-9 5z" fill="#fff"/></svg>
    <div class="bar"><i></i></div>
  </div>
</div>

<h2 class="section-title testimonials-title abs">Testimonials</h2>

<article class="testimonial first abs">
  <div class="avatar" role="img" aria-label="Customer portrait"></div>
  <p>Lindqvist Textiles provides pre-eminent customer service and I would recommend them to any progressive companies seeking a robust, reliable and state-of-the-art solution.</p>
  <span class="author">Lorem Ipsum</span>
</article>
<article class="testimonial second abs">
  <div class="avatar" role="img" aria-label="Customer portrait"></div>
  <p>Lindqvist Textiles provides pre-eminent customer service and I would recommend them to any progressive companies seeking a robust, reliable and state-of-the-art solution.</p>
  <span class="author">Lorem Ipsum</span>
</article>

<footer class="site-footer abs"></footer>
<div class="footer-brand abs">
  <div class="name"><span class="mark"></span>Bright Nook</div>
  <div class="tagline">Quality Commercial &amp; Residential Cleaning</div>
</div>
<div class="footer-info abs">
  <div style="font-size:11px">Home &nbsp;|&nbsp; About Us &nbsp;|&nbsp; Contact Us</div>
  <div>hello@brightnook.example</div>
  <div>Copyright © 2014 Bright Nook. All Rights Reserved.</div>
</div>

</body>
</html>
```